Birch And Harbor Website A Website design for book editing

A website design for book editing

Our proofreading, editing and manuscript review packages are specifically tailored to help you publish the best possible version of your story.

NEED HELP PUBLISHING A BESTSELLER?

If you’re looking for professional book editing services from senior publishing industry insiders, look no further. Besides editing, we can also answer all your publishing questions and get you started building your author platform.

OUR SERVICES

We've carefully structured our packages to maximize value for every budget.

PRICING

$.02
PER WORD
Proofreading
Line Edit (Copy-editing)
Fix spelling and grammar
Sales copy/summary revision

$.04
PER WORD
Proofreading
Line Edit (Copy-editing)
Fix spelling and grammar
Organization and content
Plot and pacing
Manuscript Review

$.06
PER WORD
Proofreading
Line Edit (Copy-editing)
Fix spelling and grammar
Organization and content
Plot and pacing
Manuscript Review
Formatting (print and ebook)
Pre-publication proofread

OUR PROCESS

Send us a sample of your book. Our caffeine-fueled, eagle-eyed editors will go through it and then email you with their comments and suggestions. You can ask them any questions you want. They will look for…

Typos and grammatical errors.
Spelling and word choice issues
Punctuation and style
Word choice, clarity and flow.
Sentence structure and craft
If your writing is already clean, then they’ll discuss bigger picture things with you, like theme, concept, purpose, audience, potential market and branding (including title, subtitle, and tagline or elevator pitch).

Once you feel comfortable and confident in an editor’s expertise, skill and knowledge, and are ready to move ahead, we’ll send an invoice for the first half of the total word count so the editor can get started. We’ll charge the rest when the project is close to completion.

Target Market(s)

Authors

Industry/Entity Type

Book Publisher

Coding

Coded - Design and coding required

Number of Pages Required

1 page

Requirements
Must have
• OUR SERVICES
• We've carefully structured our packages to maximize value for every budget.
• PRICING
• $.02
• PER WORD
• Proofreading
• Line Edit (Copy-editing)
• Fix spelling and grammar
• Sales copy/summary revision
• $.04
• PER WORD
• Proofreading
• Organization and content
• Plot and pacing
• Manuscript Review
• $.06
• PER WORD
• Proofreading
• Plot and pacing
• Manuscript Review
• Formatting (print and ebook)
• Pre-publication proofread

```html
<!DOCTYPE html>
<html lang="en">
<head>
<meta charset="utf-8">
<title>Birch And Harbor – Book Editing</title>
<link href="https://fonts.googleapis.com/css2?family=Lato:ital,wght@0,400;0,700;0,900;1,400&display=swap" rel="stylesheet">
<style>
:root{
  --red:#d0112b;
  --ink:#1e1e1e;
  --text:#444;
  --muted:#555;
  --band:#f2f2f2;
  --dark:#1c1c1c;
  --white:#fff;
}
*{box-sizing:border-box;margin:0;padding:0}
html,body{width:1200px;height:3066px;overflow:hidden}
body{position:relative;background:var(--white);font-family:'Lato',sans-serif;color:var(--text)}
.abs{position:absolute}
.center{left:0;width:1200px;text-align:center}

/* header */
.site-header{top:0;left:0;width:1200px;height:131px;background:var(--white)}
.brand{left:78px;top:50px;display:flex;align-items:center;gap:10px;font-weight:900;font-size:30px;color:var(--red)}
.brand-dot{width:16px;height:16px;border-radius:50%;background:var(--red)}
.main-nav{top:58px;left:0;width:1200px;font-size:13px;font-weight:700;color:#333;letter-spacing:.3px}
.main-nav span{position:absolute;transform:translateX(-50%);white-space:nowrap}
.main-nav .active{color:var(--red)}

/* hero */
.hero{top:131px;left:0;width:1200px;height:514px;background:linear-gradient(120deg,#8a6a4c 0%,#5a4535 35%,#3b3533 60%,#6b5040 100%)}
.hero-title{top:300px;font-size:45px;font-weight:900;color:var(--white);line-height:52px;letter-spacing:.5px}
.hero-dots{top:545px;left:570px;display:flex;gap:8px}
.hero-dots i{width:10px;height:10px;border-radius:50%;background:var(--white)}
.hero-dots i.on{background:var(--red)}

/* shared */
.section-title{font-size:30px;font-weight:900;color:var(--red);letter-spacing:.5px}
.pill{display:flex;align-items:center;justify-content:center;width:180px;height:47px;border-radius:24px;background:var(--ink);color:var(--white);font-size:14px;font-weight:700;left:510px}

/* welcome */
.welcome-text{top:764px;left:100px;width:1000px;text-align:center;font-size:15px;line-height:26px;color:var(--muted)}

/* services & pricing */
.services-band{top:960px;left:0;width:1200px;height:620px;background:var(--band)}
.services-intro{top:1040px;font-size:16px;color:var(--muted)}
.pricing-label{top:1068px;font-size:13px;font-weight:900;letter-spacing:3px;color:var(--ink)}
.service{width:300px;height:450px;text-align:center}
.service-ring{width:140px;height:140px;border-radius:50%;border:3px solid var(--red);background:var(--white);margin:0 auto;display:flex;align-items:center;justify-content:center}
.service h3{margin-top:20px;font-size:23px;font-weight:900;color:var(--red);line-height:28px}
.price{margin-top:8px;font-size:32px;font-weight:900;color:var(--ink);line-height:34px}
.per-word{font-size:12px;font-weight:700;letter-spacing:2px;color:var(--muted);line-height:16px}
.features{margin-top:10px;list-style:none;font-size:14px;line-height:20px;color:var(--muted)}
.service .more{position:absolute;left:0;right:0;bottom:0;font-size:14px;font-weight:900;color:var(--ink)}

/* process */
.process{top:1580px;left:0;width:1200px;height:690px}
.process-title{top:1675px;font-size:30px;font-weight:900;color:var(--white);letter-spacing:.5px}
.step-text{width:300px;text-align:center;font-size:17px;line-height:23px;color:var(--white)}
.look-title{top:2095px;font-size:17px;color:var(--white)}
.checks{font-size:14px;color:var(--white);white-space:nowrap}
.checks span::before{content:"✔";margin-right:10px;font-size:12px}

/* reviews */
.quote{top:2362px;left:130px;width:940px;text-align:center;font-style:italic;font-size:15px;line-height:28px;color:var(--muted)}
.review-name{top:2440px;font-size:14px;font-weight:900;color:var(--red)}
.avatar{top:2472px;left:551px;width:98px;height:98px;border-radius:50%;background:radial-gradient(circle at 50% 40%,#d9c7b6,#8f8a86)}
.arrow{font-size:34px;color:#333;top:2420px;font-weight:400}

/* footer */
.footer{top:2720px;left:0;width:1200px;height:346px}
.footer-brand{top:2770px;font-size:22px;font-weight:900;color:var(--red)}
.footer-nav{top:2860px;left:0;width:1200px;font-size:13px;font-weight:700;color:#333}
.footer-nav span{position:absolute;transform:translateX(-50%);white-space:nowrap}
.copyright{top:2893px;font-size:13px;color:var(--muted)}
.social{top:2935px;left:504px;display:flex;gap:22px}
.social i{width:20px;height:20px;border-radius:50%;background:#333}
</style>
</head>
<body>

<header class="site-header abs">
  <div class="brand abs"><span class="brand-dot"></span>Birch And Harbor</div>
  <nav class="main-nav abs">
    <span class="active" style="left:407px">HOME</span>
    <span style="left:499px">ABOUT US</span>
    <span style="left:599px">SERVICES</span>
    <span style="left:695px">PROCESS</span>
    <span style="left:791px">REVIEWS</span>
    <span style="left:875px">BLOG</span>
    <span style="left:967px">RESOURCES</span>
    <span style="left:1083px">CONTACT US</span>
  </nav>
</header>

<section class="hero abs" role="img" aria-label="Photo of hands typing on a laptop at a wooden desk with pencils and a tablet"></section>
<svg class="abs" style="top:520px;left:0" width="1200" height="130" viewBox="0 0 1200 130" aria-hidden="true">
  <path d="M0 60 C250 145 420 120 700 50 C900 0 1060 20 1200 80 L1200 130 L0 130 Z" fill="#fff"/>
</svg>
<h1 class="hero-title abs center">NEED HELP PUBLISHING<br>A BESTSELLER?</h1>
<div class="hero-dots abs"><i class="on"></i><i></i><i></i><i></i></div>

<section>
  <h2 class="section-title abs center" style="top:700px">WELCOME TO OUR WEBSITE</h2>
  <p class="welcome-text abs">If you’re looking for professional book editing services from senior publishing industry insiders, look no further. Besides editing, we can also answer all your publishing questions and get you started building your author platform.</p>
  <div class="pill abs" style="top:850px">READ MORE</div>
</section>

<section>
  <div class="services-band abs"></div>
  <svg class="abs" style="top:1130px;left:0" width="1200" height="450" viewBox="0 0 1200 450" aria-hidden="true">
    <path d="M0 30 Q600 -20 1200 30 L1200 450 L0 450 Z" fill="#fff"/>
  </svg>
  <h2 class="section-title abs center" style="top:993px">OUR SERVICES</h2>
  <p class="services-intro abs center">We've carefully structured our packages to maximize value for every budget.</p>
  <p class="pricing-label abs center">PRICING</p>

  <div class="service abs" style="left:89px;top:1100px">
    <div class="service-ring">
      <svg width="60" height="60" viewBox="0 0 64 64" fill="none" stroke="#1e1e1e" stroke-width="3" stroke-linejoin="round"><path d="M18 8h20l10 10v16"/><path d="M18 8v48h16"/><circle cx="44" cy="44" r="10"/><path d="M39 44l4 4 6-7"/></svg>
    </div>
    <h3>PROOFREADING</h3>
    <p class="price">$.02</p>
    <p class="per-word">PER WORD</p>
    <ul class="features">
      <li>Proofreading</li>
      <li>Line Edit (Copy-editing)</li>
      <li>Fix spelling and grammar</li>
      <li>Sales copy/summary revision</li>
    </ul>
    <div class="more">READ MORE</div>
  </div>
  <div class="service abs" style="left:449px;top:1100px">
    <div class="service-ring">
      <svg width="60" height="60" viewBox="0 0 64 64" fill="none" stroke="#1e1e1e" stroke-width="3" stroke-linejoin="round"><path d="M12 8h30v48H12z"/><path d="M18 18h16M18 26h16M18 34h10M18 46c4-4 6 4 10 0"/><path d="M50 14l6 6-18 18-8 2 2-8z"/></svg>
    </div>
    <h3>EDITING</h3>
    <p class="price">$.04</p>
    <p class="per-word">PER WORD</p>
    <ul class="features">
      <li>Proofreading</li>
      <li>Line Edit (Copy-editing)</li>
      <li>Fix spelling and grammar</li>
      <li>Organization and content</li>
      <li>Plot and pacing</li>
      <li>Manuscript Review</li>
    </ul>
    <div class="more">READ MORE</div>
  </div>
  <div class="service abs" style="left:809px;top:1100px">
    <div class="service-ring">
      <svg width="60" height="60" viewBox="0 0 64 64" fill="none" stroke="#1e1e1e" stroke-width="3" stroke-linejoin="round"><path d="M18 8h30v44a6 6 0 0 1-6 6H14a6 6 0 0 1-6-6v-4h34v4"/><path d="M18 8v40"/><path d="M24 18h16M24 26h16M24 34h16"/><rect x="24" y="14" width="16" height="6" fill="#1e1e1e"/></svg>
    </div>
    <h3>MANUSCRIPT</h3>
    <p class="price">$.06</p>
    <p class="per-word">PER WORD</p>
    <ul class="features">
      <li>Proofreading</li>
      <li>Line Edit (Copy-editing)</li>
      <li>Fix spelling and grammar</li>
      <li>Organization and content</li>
      <li>Plot and pacing</li>
      <li>Manuscript Review</li>
      <li>Formatting (print and ebook)</li>
      <li>Pre-publication proofread</li>
    </ul>
    <div class="more">READ MORE</div>
  </div>
</section>

<section>
  <svg class="process abs" viewBox="0 0 1200 690" aria-hidden="true">
    <path d="M0 80 Q600 -40 1200 80 L1200 690 L0 690 Z" fill="#1c1c1c"/>
    <g fill="none" stroke="#fff" stroke-width="3">
      <path d="M237 210H523M597 210H883M957 210H1068a15 15 0 0 1 15 15V381a15 15 0 0 1-15 15H957M883 396H597"/>
      <path d="M560 433V482"/>
      <circle cx="200" cy="210" r="37"/><circle cx="560" cy="210" r="37"/><circle cx="920" cy="210" r="37"/>
      <circle cx="920" cy="396" r="37"/><circle cx="560" cy="396" r="37"/>
      <path d="M372 202l10 8-10 8M732 202l10 8-10 8M1075 300l8 10 8-10M752 388l-10 8 10 8M552 474l8 10 8-10"/>
    </g>
    <g fill="#fff">
      <rect x="190" y="201" width="20" height="13" rx="1" fill="none" stroke="#fff" stroke-width="2.5"/><rect x="185" y="215" width="30" height="3"/>
      <path d="M546 210q14-14 28 0q-14 14-28 0z"/><circle cx="560" cy="210" r="4" fill="#1c1c1c"/>
      <rect x="908" y="202" width="24" height="17" rx="1"/><path d="M908 203l12 9 12-9" fill="none" stroke="#1c1c1c" stroke-width="2"/>
      <circle cx="920" cy="396" r="12"/><text x="920" y="402" text-anchor="middle" font-family="Lato,sans-serif" font-weight="900" font-size="16" fill="#1c1c1c">?</text>
      <path d="M551 384h12l6 6v18h-18z"/><path d="M555 394h10M555 399h10M555 404h7" stroke="#1c1c1c" stroke-width="1.5"/>
    </g>
  </svg>
  <h2 class="process-title abs center">OUR PROCESS</h2>
  <p class="step-text abs" style="left:50px;top:1852px">Send us a sample of<br>your book.</p>
  <p class="step-text abs" style="left:410px;top:1852px">Our caffeine-fueled, eagle-eyed<br>editors will go through it.</p>
  <p class="step-text abs" style="left:770px;top:1852px">Email you with their comments<br>and suggestions.</p>
  <p class="step-text abs" style="left:770px;top:2032px">You can ask them any questions<br>you want.</p>
  <p class="look-title abs center">They will look for...</p>
  <div class="checks abs" style="left:302px;top:2143px"><span>Typos and grammatical errors.</span></div>
  <div class="checks abs" style="left:583px;top:2143px"><span>Spelling and word choice issues</span></div>
  <div class="checks abs" style="left:314px;top:2175px"><span>Punctuation and style</span></div>
  <div class="checks abs" style="left:576px;top:2175px"><span>Word choice, clarity and flow.</span></div>
  <div class="checks abs" style="left:450px;top:2207px"><span>Sentence structure and craft</span></div>
</section>

<section>
  <h2 class="section-title abs center" style="top:2305px">REVIEWS</h2>
  <p class="quote abs">“ Our proofreading, editing and manuscript review packages are specifically tailored to help you publish the best possible version of your story. ”</p>
  <span class="arrow abs" style="left:72px">‹</span>
  <span class="arrow abs" style="left:1108px">›</span>
  <p class="review-name abs center">-NAME HEADING</p>
  <div class="avatar abs" role="img" aria-label="Portrait photo of the reviewer"></div>
  <div class="pill abs" style="top:2610px;width:182px;left:509px">READ ALL REVIEWS</div>
</section>

<footer>
  <svg class="footer abs" viewBox="0 0 1200 346" aria-hidden="true">
    <path d="M0 20 Q600 -20 1200 20 L1200 346 L0 346 Z" fill="#f2f2f2"/>
  </svg>
  <p class="footer-brand abs center">Birch And Harbor</p>
  <nav class="footer-nav abs">
    <span style="left:251px">HOME</span>
    <span style="left:342px">ABOUT US</span>
    <span style="left:442px">SERVICES</span>
    <span style="left:539px">PROCESS</span>
    <span style="left:634px">REVIEWS</span>
    <span style="left:718px">BLOG</span>
    <span style="left:811px">RESOURCES</span>
    <span style="left:927px">CONTACT US</span>
  </nav>
  <p class="copyright abs center">Copyright 2018 Company Name. All Rights Reserved.</p>
  <div class="social abs" aria-label="Social links"><i></i><i></i><i></i><i></i><i></i></div>
</footer>

</body>
</html>
```